Flyer Design Project

We need a flyer design for a 1 year old domestic cleaning company based in Wiltshire, England. We provide households with high quality, hard working cleaners. We would like to see designs which use blue (the colour on the logo attatched). The final design should communicate a clean, premier and thorough service in a clear and bold way. We would like the flyer to be A5 with a single sided design. We have attached an A5 word document with the words we would like to be used in the design, what we need is for you to give it some life, colour, artwork and a professional touch. We are perfectionsists which we would like to illustrate to our customer through this flyer.
Updates

payment has been guaranteed!

Sorry..... please no pictures of females on the designs. many thanks

Target Market(s)

females with higher than average income, aged 30-50. Have families and work 9-5.

Industry/Entity Type

It Company

Requirements
Must have
• The flyer must include the logo attatched and the words in the A5 document attatched. With RELIABLE CLEANERS preferably the headline. A5 - single sided.
The Flyer must also include our introductory offer.....
First Clean FREE
Allow us to demonstrate our standards

this should be emphasised.

PLEASE NOTE: can this be added to the list of words on the flyer please:

Ironing service - one day turn around
Nice to have
• some pictures - nothing cheesey. Again, pictures should communicate our modern professional approach.

```html
<!DOCTYPE html>
<html lang="en">
<head>
<meta charset="utf-8">
<title>Brightmoor Cleaners – Flyer</title>
<link rel="stylesheet" href="https://fonts.googleapis.com/css2?family=Gentium+Book+Plus:wght@400;700&family=PT+Sans&display=swap">
<style>
  :root {
    --blue: #2f7cf0;
    --blue-deep: #1450c8;
    --blue-light: #5fa3ff;
    --grey: #e4e8e9;
    --wood-dark: #5a2a14;
    --wood-mid: #9a5528;
    --wood-light: #d3955a;
    --maroon: #5e1518;
    --ink: #111111;
    --white: #ffffff;
    --bullet: #d8c21a;
  }
  * { margin: 0; padding: 0; box-sizing: border-box; }
  html, body { width: 1200px; height: 839px; overflow: hidden; background: var(--grey); }
  .flyer {
    position: relative;
    width: 1200px;
    height: 839px;
    overflow: hidden;
    font-family: "Gentium Book Plus", Georgia, serif;
  }
  .flyer-art { position: absolute; inset: 0; }
  .headline, .offer, .offer-intro, .features, .brand, .tagline, .contact, .badge-text { position: absolute; }
  .headline {
    left: 32px; top: 8px;
    font-size: 64px; line-height: 1.1; letter-spacing: 3px;
    color: var(--white);
    text-shadow: 2px 2px 4px rgba(0,0,0,.6);
    font-weight: 400;
  }
  .offer {
    left: 298px; top: 74px;
    font-size: 70px; line-height: 1.1; letter-spacing: 3px;
    color: var(--white);
    text-shadow: 2px 2px 4px rgba(0,0,0,.6);
    font-weight: 400;
  }
  .offer-intro {
    left: 278px; top: 155px;
    font-size: 22px; line-height: 1.2; letter-spacing: 1.5px;
    color: var(--white);
    text-shadow: 1px 1px 3px rgba(0,0,0,.65);
  }
  .features {
    left: 274px; top: 188px;
    display: grid;
    grid-template-columns: 304px 320px;
    list-style: none;
  }
  .features li {
    font-size: 22px; line-height: 30px; letter-spacing: 1.5px;
    color: var(--white);
    text-shadow: 1px 1px 3px rgba(0,0,0,.65);
    display: flex; align-items: center; gap: 12px;
  }
  .features li::before {
    content: "";
    width: 12px; height: 12px; border-radius: 50%;
    background: radial-gradient(circle at 35% 35%, #fff6a0, var(--bullet) 60%, #8a7a00);
    flex: none;
  }
  .badge-text {
    left: 960px; top: 104px; width: 220px;
    text-align: center;
    color: var(--white);
    font-size: 23px; line-height: 31px; letter-spacing: .5px;
    text-shadow: 1px 1px 2px rgba(0,0,0,.45);
  }
  .badge-text .badge-title { font-weight: 700; }
  .brand {
    left: 43px; top: 508px;
    display: flex; align-items: flex-end; gap: 12px;
  }
  .brand-mark { width: 111px; height: 138px; background: var(--blue); }
  .brand-name {
    font-family: "PT Sans", Arial, sans-serif;
    font-size: 54px; line-height: 1; color: var(--ink);
  }
  .tagline {
    left: 163px; top: 668px;
    font-family: "PT Sans", Arial, sans-serif;
    font-size: 32px; color: var(--ink);
  }
  .contact {
    top: 766px; height: 45px;
    display: flex; align-items: center; padding-left: 12px;
    background: linear-gradient(180deg, var(--blue-light), var(--blue) 55%, var(--blue-deep));
    border-radius: 4px;
    box-shadow: 2px 3px 4px rgba(0,0,0,.3);
    color: var(--white);
    font-size: 25px; letter-spacing: 1px; white-space: nowrap;
  }
  .contact-email { left: 20px; width: 522px; }
  .contact-phone { left: 550px; width: 399px; }
</style>
</head>
<body>
<main class="flyer">
  <svg class="flyer-art" width="1200" height="839" viewBox="0 0 1200 839">
    <defs>
      <linearGradient id="wood" x1="0" y1="0" x2="1" y2=".7">
        <stop offset="0" stop-color="#c9a88a"/>
        <stop offset=".12" stop-color="var(--wood-mid)"/>
        <stop offset=".35" stop-color="var(--wood-light)"/>
        <stop offset=".55" stop-color="#b8703a"/>
        <stop offset=".8" stop-color="var(--wood-mid)"/>
        <stop offset="1" stop-color="var(--wood-dark)"/>
      </linearGradient>
      <radialGradient id="machineShade" cx=".88" cy=".35" r=".35">
        <stop offset="0" stop-color="var(--maroon)" stop-opacity=".85"/>
        <stop offset=".6" stop-color="#4a2a1c" stop-opacity=".55"/>
        <stop offset="1" stop-color="#4a2a1c" stop-opacity="0"/>
      </radialGradient>
      <linearGradient id="topGlow" x1="0" y1="0" x2="0" y2="1">
        <stop offset="0" stop-color="#e8d6c2" stop-opacity=".45"/>
        <stop offset=".25" stop-color="#e8d6c2" stop-opacity="0"/>
      </linearGradient>
      <radialGradient id="badgeFill" cx=".35" cy=".35" r=".75">
        <stop offset="0" stop-color="var(--blue-light)"/>
        <stop offset=".6" stop-color="var(--blue)"/>
        <stop offset="1" stop-color="var(--blue-deep)"/>
      </radialGradient>
      <radialGradient id="dusterPhoto" cx=".35" cy=".3" r=".8">
        <stop offset="0" stop-color="#e0442c"/>
        <stop offset=".45" stop-color="#b5261a"/>
        <stop offset=".75" stop-color="#6e3a28"/>
        <stop offset="1" stop-color="#4a2418"/>
      </radialGradient>
      <linearGradient id="vacuumPhoto" x1="0" y1="0" x2="0" y2="1">
        <stop offset="0" stop-color="#f1f3f4"/>
        <stop offset=".5" stop-color="#c9ccce"/>
        <stop offset=".72" stop-color="#8a5a3c"/>
        <stop offset="1" stop-color="#5a3320"/>
      </linearGradient>
      <linearGradient id="dishPhoto" x1="0" y1="0" x2="0" y2="1">
        <stop offset="0" stop-color="#c08a5e"/>
        <stop offset=".4" stop-color="#e9e4de"/>
        <stop offset=".75" stop-color="#d6d2cc"/>
        <stop offset="1" stop-color="#f4f2ef"/>
      </linearGradient>
    </defs>

    <g class="hero-photo" role="img" aria-label="Photo of a floor polisher cleaning a polished wooden floor">
      <rect x="0" y="0" width="1200" height="839" fill="url(#wood)"/>
      <rect x="0" y="0" width="1200" height="839" fill="url(#machineShade)"/>
      <rect x="0" y="0" width="1200" height="839" fill="url(#topGlow)"/>
    </g>

    <polygon class="diagonal-band" points="0,175 1200,736 1200,760 0,270" fill="var(--blue)"/>
    <polygon class="lower-panel" points="0,270 1200,760 1200,839 0,839" fill="var(--grey)"/>

    <polygon class="ironing-badge"
      fill="url(#badgeFill)"
      points="1062,24 1074,50 1091,30 1099,57 1119,42 1121,70 1144,60 1140,87 1165,84 1155,109 1180,111 1165,133 1189,142 1168,158 1187,171 1163,182 1177,203 1150,207 1158,232 1131,230 1133,256 1109,247 1104,273 1084,259 1074,284 1058,265 1046,288 1034,266 1016,284 1010,257 987,271 985,244 961,252 963,225 937,227 945,202 920,197 933,175 910,165 929,148 909,135 932,121 915,103 940,97 929,74 955,74 949,48 974,55 974,29 998,40 1003,14 1023,29 1033,6 1046,26"/>

    <circle class="photo-ring" cx="509" cy="407" r="143" fill="var(--grey)"/>
    <circle class="photo" role="img" aria-label="Photo of a feather duster dusting a wooden surface" cx="509" cy="407" r="131" fill="url(#dusterPhoto)"/>

    <circle class="photo-ring" cx="810" cy="567" r="109" fill="var(--grey)"/>
    <circle class="photo" role="img" aria-label="Photo of a man vacuuming a bright living room" cx="810" cy="567" r="99" fill="url(#vacuumPhoto)"/>

    <circle class="photo-ring" cx="1079" cy="698" r="86" fill="var(--grey)"/>
    <circle class="photo" role="img" aria-label="Photo of a plate being scrubbed under a running tap" cx="1079" cy="698" r="77" fill="url(#dishPhoto)"/>
  </svg>

  <h1 class="headline">Reliable Cleaners!</h1>
  <h2 class="offer">First Clean FREE</h2>
  <p class="offer-intro">Allow us to demonstrate our standards……</p>
  <ul class="features">
    <li>Personalised Service</li>
    <li>Insured</li>
    <li>Constantly Thorough</li>
    <li>Regular Weekly Claims</li>
    <li>Hassle Free</li>
    <li>No Contracts</li>
  </ul>

  <p class="badge-text"><span class="badge-title">Ironing Service</span><br>One Day<br>Turn Around</p>

  <div class="brand">
    <span class="brand-mark"></span>
    <span class="brand-name">Brightmoor Cleaners</span>
  </div>
  <p class="tagline">Premier Domestic Cleaners</p>

  <p class="contact contact-email">Email: hello@brightmoorcleaners.co.uk</p>
  <p class="contact contact-phone">Call our hotline: 07700900123</p>
</main>
</body>
</html>
```